Bry7Legal Letterhead

Need a new letterhead for my law firm.
IDENTIFYING INFORMATION BELOW:
Anselmo R Quintara III
Attorney at Law
Address: 2847 Larkspur Blvd, Ste 300, Dallas, TX 75204
Phone: 877-482-6017
Fax: 469-738-1452
Email: bry@bry7legal.example
Website: www.bry7legal.example

Colors
0054AA
0677BA
7BADD7
CADEEF
E8F1F8

Requirements
Must have
• Logo needs to be on the letterhead, along with identifying information which is included in the project description.

```html
<!DOCTYPE html>
<html lang="en">
<head>
<meta charset="utf-8">
<title>Bry7Legal Letterhead</title>
<link href="https://fonts.googleapis.com/css2?family=Montserrat:wght@400;500;700;800&family=Arimo:wght@400;700&display=swap" rel="stylesheet">
<style>
  :root {
    --brand-navy: #0054AA;
    --brand-blue: #0677BA;
    --brand-sky: #7BADD7;
    --brand-mist: #CADEEF;
    --brand-ice: #E8F1F8;
    --ink: #111111;
    --ink-soft: #333333;
    --body-grey: #8a8a8a;
    --rule: #9a9a9a;
    --paper: #ffffff;
  }
  * { margin: 0; padding: 0; box-sizing: border-box; }
  html, body { width: 1200px; height: 1200px; overflow: hidden; }
  body {
    background: var(--brand-mist);
    font-family: "Montserrat", sans-serif;
    position: relative;
  }
  .letterhead {
    position: absolute;
    left: 190px; top: 20px;
    width: 821px; height: 1160px;
    background: var(--paper);
  }
  .brand { position: absolute; left: 54px; top: 58px; width: 279px; text-align: center; }
  .brand-name {
    font-family: "Montserrat", sans-serif;
    font-weight: 800; font-size: 38px; line-height: 40px;
    letter-spacing: 1px; color: var(--ink);
  }
  .brand-tagline {
    font-family: "Montserrat", sans-serif;
    font-weight: 500; font-size: 17px; letter-spacing: 2.6px;
    color: var(--ink); margin-top: 4px;
  }
  .attorney {
    position: absolute; left: 456px; top: 46px;
    font-family: "Arimo", sans-serif; font-size: 13.5px; line-height: 16px; color: var(--ink-soft);
  }
  .attorney-name { color: var(--brand-navy); font-weight: 700; }
  .attorney-address { margin-top: 9px; line-height: 17px; }
  .header-divider {
    position: absolute; left: 630px; top: 48px; width: 1px; height: 71px; background: var(--rule);
  }
  .contact-list {
    position: absolute; left: 648px; top: 46px; list-style: none;
    font-family: "Arimo", sans-serif; font-size: 13.5px; color: var(--ink-soft);
  }
  .contact-list li { display: flex; align-items: center; height: 19.3px; }
  .contact-list svg { width: 11px; height: 11px; margin-right: 7px; fill: var(--brand-blue); }
  .header-rule { position: absolute; left: 54px; top: 131px; width: 712px; height: 1px; background: var(--rule); }

  .recipient { position: absolute; left: 83px; top: 258px; }
  .recipient-label { font-size: 14px; letter-spacing: 2px; color: var(--ink-soft); }
  .recipient-name { font-size: 14px; color: var(--brand-blue); margin-top: 8px; }
  .recipient-lines { margin-top: 6px; font-size: 11.5px; line-height: 18px; color: var(--body-grey); }
  .letter-date { position: absolute; right: 84px; top: 260px; font-size: 11.5px; color: var(--ink-soft); }

  .letter-body {
    position: absolute; left: 83px; top: 415px; width: 656px;
    font-size: 12.3px; line-height: 14.6px; color: var(--body-grey); text-align: justify;
  }
  .letter-body p { margin-bottom: 14.6px; }

  .signature-mark {
    position: absolute; left: 83px; top: 822px; width: 140px; height: 28px;
    background: var(--brand-ice); border-radius: 3px;
  }
  .signer { position: absolute; left: 81px; top: 862px; }
  .signer-name { font-size: 13.5px; color: var(--ink-soft); }
  .signer-title { font-size: 11px; color: var(--body-grey); margin-top: 3px; }
</style>
</head>
<body>
<main class="letterhead">
  <header>
    <div class="brand">
      <div class="brand-name">BRY7LEGAL</div>
      <div class="brand-tagline">LAW WITH CLARITY</div>
    </div>
    <div class="attorney">
      <div class="attorney-name">Anselmo R Quintara III</div>
      <div>Attorney at Law</div>
      <div class="attorney-address">2847 Larkspur Blvd<br>Ste 300, Dallas, TX 75204</div>
    </div>
    <div class="header-divider"></div>
    <ul class="contact-list">
      <li><svg viewBox="0 0 24 24"><path d="M6.6 10.8a15.1 15.1 0 0 0 6.6 6.6l2.2-2.2c.3-.3.7-.4 1-.2 1.1.4 2.3.6 3.6.6.6 0 1 .4 1 1V20c0 .6-.4 1-1 1C10.6 21 3 13.4 3 4c0-.6.4-1 1-1h3.5c.6 0 1 .4 1 1 0 1.3.2 2.5.6 3.6.1.3 0 .7-.2 1z"/></svg>877-482-6017</li>
      <li><svg viewBox="0 0 24 24"><path d="M6 2h12v5H6zM3 8h18a1 1 0 0 1 1 1v8h-4v5H6v-5H2V9a1 1 0 0 1 1-1zm5 8v4h8v-4z"/></svg>469-738-1452</li>
      <li><svg viewBox="0 0 24 24"><path d="M2 5h20v14H2zm2 2v.5l8 5 8-5V7l-8 5z"/></svg>bry@bry7legal.example</li>
      <li><svg viewBox="0 0 24 24"><path d="M12 2a10 10 0 1 0 0 20 10 10 0 0 0 0-20zm-1 2.1V8H7.3A8 8 0 0 1 11 4.1zM4.3 10H8v4H4.3a8 8 0 0 1 0-4zm5.7 0h4v4h-4zm6 0h3.7a8 8 0 0 1 0 4H16zM13 4.1A8 8 0 0 1 16.7 8H13zM7.3 16H11v3.9A8 8 0 0 1 7.3 16zm5.7 0h3.7a8 8 0 0 1-3.7 3.9z"/></svg>www.bry7legal.example</li>
    </ul>
    <div class="header-rule"></div>
  </header>

  <section class="recipient">
    <div class="recipient-label">TO</div>
    <div class="recipient-name">Delia Fenwright</div>
    <div class="recipient-lines">
      Human Resources<br>
      Norvale Systems Inc.<br>
      4410-B Harlow Point, Westbrook<br>
      K27 USA
    </div>
  </section>
  <div class="letter-date">Friday, 01/01/2018</div>

  <article class="letter-body">
    <p>Lorem ipsum dolor sit amet, consectetuer adipiscing elit, sed diam nonmmy nibh euismod tincidunt ut laoreet dolore magna aliquam erat volutpat. Ut wisi enim ad minim veniam, quis nostrud exerci tationmcorper suscipit lobortis nisl ut aliquip ex ea commodo consequat. Duis autem vel eum iriure dolor in hendrerit in vulputate velit esse molestie consequat, vel illum dolore eu feugiat nulla facilisis at vero eros et accumsan et iusto odio dignissim qui blandit praesent luptatum zzril delenit augue duis dolore te feugait nulla facilisi.</p>
    <p>Nam liber tempor cum soluta nobis eleifend option congue nihil imprdiet doming id quod mazim placerat facer possim assum. Typi non habent claritatem insitam;</p>
    <p>Est usus legentis in iis qui facit eorum claritatem.</p>
    <p>Investigationes demonstraverunt lectores legere me lius quod ii legunt saepius. Claritas est etiam processus dynamicus, qui sequitur mutationem consuetudium lectorum. Mirum est notare quam littera gothica, quam nunc putamus parum claram, anteposuerit litterarum formas humanitatis per seacula quarta decima et quinta decima. Eodem modo typi, qui nunc nobis videntur parum clari, fiant sollemnes in futurum.</p>
    <p>consectetuer adipiscing elit, sed diam nonummy nibh euismod tincidunt ut laoreet dolore magna aliquam erat volutpat. Ut wisi enim ad minim veniam, quis nostrud exerci tation ullamcorper suscipit lobortis nisl ut aliquip ex ea commodo consequat. Duis autem vel eum iriure dolor in hendrerit in vulputate velit esse molestie consequat, vel illum dolore eu feugiat nulla facilisis at vero eros et accumsan et iusto odio dignissim qui blandit praesent luptatum zzril delenit augue duis dolore te feugait nulla facilisi.</p>
    <p>Nam liber tempor cum soluta nobis eleifend option congue nihil imperdiet .</p>
  </article>

  <div class="signature-mark" role="img" aria-label="Handwritten signature of the signer"></div>
  <footer class="signer">
    <div class="signer-name">Peter Hallorin</div>
    <div class="signer-title">Managing Director</div>
  </footer>
</main>
</body>
</html>
```